Business Cards for new orthopaedic surgery practice

My husband and I are starting our own orthopaedic surgery practice. We are looking for a business card that is uniform, but one will have my name/title and the other will have his. You can just create one design with my name on it for now. But when I choose your design as the winning design I will ask that you add another copy with his name/title.

We are looking for classy, simple, elite all in one. We like dark blues/a little gold/yellow. Something that goes with our logo. We want our logo incorporated. Here is all the info you need:
Business name: RV Bone & Vitality Center
Location: 38517 North Willowmere Ave
Coral Springs, FL 33071
Phone: 954-218-4063
Fax: 954-582-7341
Email: info@myrvbonecare.example

Names: Lydia Vance, M.D.
Board Certified Hand and Upper Extremity Surgeon

Ebo Dansu, M.D.
Board Certified Hip & Knee Replacement/General Orthopaedic Surgeon

Can decide what you want to put on the back. Maybe a slogan:
Rooted in Care. Focused on You

I am just going to upload our logo. The only thing is if we select you as the winning design, the location, and phone numbers may change. We will need your help to update that once fully solidified.

Industry/Entity Type

Medical

Contact Information for Business Card

Colors
0054AA
0677BA
7BADD7
CADEEF
E8F1F8
0094D4
00A9DD
6FCCEA
C7EBF8
E9F6FB

Requirements
Must have
• class, appeal,
Should not have
• We want to air on the side of masculine if we are looking at masculine vs. feminine feel. But we still want it classy, sophisticated, and something we will love

```html
<!DOCTYPE html>
<html lang="en">
<head>
<meta charset="utf-8">
<title>RV Bone &amp; Vitality Center — Business Card</title>
<link rel="stylesheet" href="https://fonts.googleapis.com/css2?family=Cinzel:wght@600&family=Crimson+Pro:wght@400;700&family=Poppins:wght@400&display=swap">
<style>
  :root {
    --backdrop: #d8d6d6;
    --navy: #142547;
    --navy-soft: #1b2f57;
    --white: #ffffff;
    --gold-light: #f3dc8c;
    --gold: #d8b25a;
    --gold-deep: #a9822f;
  }
  * { box-sizing: border-box; margin: 0; padding: 0; }
  html, body { width: 977px; height: 1200px; overflow: hidden; }
  body { background: var(--backdrop); position: relative; }

  .card {
    position: absolute;
    left: 44px;
    width: 889px;
    height: 507px;
    background: var(--navy);
    box-shadow: 0 6px 14px rgba(0,0,0,0.35);
    color: var(--white);
  }
  .card--front { top: 49px; }
  .card--back { top: 613px; }

  .brand {
    position: absolute;
    left: 0; right: 0;
    text-align: center;
    font-family: "Cinzel", serif;
    font-weight: 600;
    color: var(--white);
    line-height: 1.15;
  }
  .brand__mark {
    display: block;
    margin: 0 auto 12px;
    border-radius: 50%;
    border: 2px solid var(--white);
  }
  .card--front .brand { top: 140px; font-size: 31px; }
  .card--front .brand__mark { width: 34px; height: 34px; }
  .card--back .brand { top: 60px; font-size: 25px; }
  .card--back .brand__mark { width: 28px; height: 28px; }

  .gold-text {
    background: linear-gradient(180deg, var(--gold-light) 0%, var(--gold) 55%, var(--gold-deep) 100%);
    -webkit-background-clip: text;
    background-clip: text;
    color: transparent;
  }

  .tagline {
    position: absolute;
    top: 318px; left: 0; right: 0;
    text-align: center;
    font-family: "Crimson Pro", serif;
    font-weight: 700;
    font-size: 41px;
  }

  .doctors {
    position: absolute;
    left: 39px; top: 240px;
    width: 380px;
  }
  .doctor + .doctor { margin-top: 28px; }
  .doctor__name {
    font-family: "Cinzel", serif;
    font-weight: 600;
    font-size: 21px;
    line-height: 1.3;
  }
  .doctor__title {
    margin-top: 6px;
    font-family: "Crimson Pro", serif;
    font-size: 18.5px;
    line-height: 21px;
  }

  .divider {
    position: absolute;
    left: 418px; top: 240px;
    width: 2px; height: 199px;
    background: linear-gradient(180deg, var(--gold-light), var(--gold-deep));
  }

  .contact {
    position: absolute;
    left: 461px; top: 238px;
    width: 420px;
  }
  .contact__heading {
    font-family: "Cinzel", serif;
    font-weight: 600;
    font-size: 20px;
    line-height: 1.3;
    white-space: nowrap;
  }
  .contact__list { list-style: none; margin-top: 10px; }
  .contact__item {
    display: flex;
    align-items: flex-start;
    gap: 13px;
    font-family: "Poppins", sans-serif;
    font-size: 17px;
    line-height: 21px;
    min-height: 30px;
  }
  .contact__item + .contact__item { margin-top: 12px; }
  .contact__item span { padding-top: 4px; }
  .contact__icon {
    flex: 0 0 30px;
    width: 30px; height: 30px;
    border-radius: 50%;
    background: linear-gradient(180deg, var(--gold-light), var(--gold-deep));
    display: flex; align-items: center; justify-content: center;
  }
  .contact__icon svg { width: 16px; height: 16px; fill: var(--navy); }
</style>
</head>
<body>

<section class="card card--front">
  <div class="brand">
    <span class="brand__mark"></span>
    RV BONE &amp; VITALITY<br>CENTER
  </div>
  <p class="tagline gold-text">Rooted in Care. Focused on You</p>
</section>

<section class="card card--back">
  <div class="brand">
    <span class="brand__mark"></span>
    RV BONE &amp; VITALITY<br>CENTER
  </div>

  <div class="doctors">
    <div class="doctor">
      <h2 class="doctor__name gold-text">LYDIA VANCE, M.D.</h2>
      <p class="doctor__title">Board Certified Hand and<br>Upper Extremity Surgeon</p>
    </div>
    <div class="doctor">
      <h2 class="doctor__name gold-text">EBO DANSU, M.D.</h2>
      <p class="doctor__title">Board Certified Hip &amp; Knee Replacement<br>/General Orthopaedic Surgeon</p>
    </div>
  </div>

  <div class="divider"></div>

  <div class="contact">
    <h2 class="contact__heading gold-text">RV BONE &amp; VITALITY CENTER</h2>
    <ul class="contact__list">
      <li class="contact__item">
        <span class="contact__icon"><svg viewBox="0 0 24 24"><path d="M12 2a7 7 0 0 0-7 7c0 5 7 13 7 13s7-8 7-13a7 7 0 0 0-7-7zm0 9.5A2.5 2.5 0 1 1 12 6.5a2.5 2.5 0 0 1 0 5z"/></svg></span>
        <span>38517 North Willowmere Ave Coral Springs,<br>FL 33071</span>
      </li>
      <li class="contact__item">
        <span class="contact__icon"><svg viewBox="0 0 24 24"><path d="M6.6 10.8a15 15 0 0 0 6.6 6.6l2.2-2.2c.3-.3.7-.4 1-.2 1.1.4 2.3.6 3.6.6.6 0 1 .4 1 1V20c0 .6-.4 1-1 1A17 17 0 0 1 3 4c0-.6.4-1 1-1h3.5c.6 0 1 .4 1 1 0 1.3.2 2.5.6 3.6.1.3 0 .7-.2 1z"/></svg></span>
        <span>954-218-4063</span>
      </li>
      <li class="contact__item">
        <span class="contact__icon"><svg viewBox="0 0 24 24"><path d="M7 3h9v5H7zM4 9h16a1 1 0 0 1 1 1v10a1 1 0 0 1-1 1H4a1 1 0 0 1-1-1V10a1 1 0 0 1 1-1zm3 3v2h2v-2zm4 0v2h2v-2zm4 0v2h2v-2zm-8 4v2h2v-2zm4 0v2h2v-2zm4 0v2h2v-2z"/></svg></span>
        <span>954-582-7341</span>
      </li>
      <li class="contact__item">
        <span class="contact__icon"><svg viewBox="0 0 24 24"><path d="M12 2a10 10 0 1 0 0 20 10 10 0 0 0 0-20zm6.9 9h-3a15 15 0 0 0-1.3-5.6A8 8 0 0 1 18.9 11zM12 4c.9 1.2 1.8 3.6 1.9 7h-3.8c.1-3.4 1-5.8 1.9-7zM9.4 5.4A15 15 0 0 0 8.1 11h-3a8 8 0 0 1 4.3-5.6zM5.1 13h3a15 15 0 0 0 1.3 5.6A8 8 0 0 1 5.1 13zM12 20c-.9-1.2-1.8-3.6-1.9-7h3.8c-.1 3.4-1 5.8-1.9 7zm2.6-1.4a15 15 0 0 0 1.3-5.6h3a8 8 0 0 1-4.3 5.6z"/></svg></span>
        <span>info@myrvbonecare.example</span>
      </li>
    </ul>
  </div>
</section>

</body>
</html>
```